Mortgage Protection Insurance Flyer

The target audience are new home owners so the design needs to be clean and simple.

This a primarily for Final Expense Insurance, but need an area where it says "We Also Specialize In:"
- Medicare Supplement Insurance (MediGap)
- Annuities
- Final Expense

All flyer versions need to be editable. Colors to be used are red, white or black. Refer to my website for colors and photos (corvantshield.com). Will attach my logo and a flyer that I found online that is the format that I am looking for (for 8.5 in. x 11 in version). Need flyer in standard letter size 8.5 in. x11 in. but also in 8.5 in. x 5.5 in and 5.0 in. x 8.0 in. All sizes to be portrait oriented. If picked as winning design, need all flyer versions in full color, also in grey scale and files in all industry file types.

Content can be taken from my website..... corvantshield.com

Do NOT submit if you are not willing to provide all versions as described above for the original project price.

Must use royalty-free stock photos please.

Target Market(s)

New homeowners looking for insurance to protect there mortgage payments

Industry/Entity Type

Life Insurance

Colors
f69fa3

Requirements
Must have
• Colors to be used are red, white or black.
• Need flyer in standard letter size 8.5 in. x11 in. but also in 3.5 in. x 8.5 in (Full Bleed 3.75 in by 8.75 in.) and 4.0 in. x 6.0 in. (Full Bleed 4.12 in x 6.12 in) Each design tailored to the size dimensions (So no squeezing 8.5 x 11 design into a 4.0 x 6.0 space.) All sizes to be portrait oriented. If picked as winning design, need all flyer versions in full color, also in grey scale and files in all file types.
• Do not need physical address on flyer, do need email address on flyer though - tkelwer@corvantshield.com
• So phone number should be prominent, email address and website address should also be contact area.
• If you can not agree to terms above, do not submit any designs.
• Need facebook & twitter logos somewhere in contact info area.
Nice to have
• See sample flyers I have attached.
• White background with red used as primary graphic color and black used as secondary graphic if needed.
• font to be used should similar to one used in logo.

```html
<!DOCTYPE html>
<html lang="en">
<head>
<meta charset="utf-8">
<title>Corvant Shield – Mortgage Protection Flyer</title>
<link rel="stylesheet" href="https://fonts.googleapis.com/css2?family=Anton&family=Rubik:wght@400;500;700;800&family=Lato:wght@400;700&display=swap">
<style>
  :root {
    --board-color: #f2b7b7;
    --board-grey: #dcdcdc;
    --ink: #1e1e1e;
  }
  * { box-sizing: border-box; margin: 0; padding: 0; }
  html, body { width: 1200px; height: 1200px; overflow: hidden; }
  body { position: relative; font-family: "Lato", sans-serif; }
  .board-half { position: absolute; top: 0; height: 1200px; }
  .board-half--color { left: 0; width: 617px; background: var(--board-color); }
  .board-half--grey { left: 617px; width: 583px; background: var(--board-grey); }

  .flyer {
    --accent: #ee1111;
    --accent-deep: #a81c22;
    --accent-top: #ff0a0a;
    --photo-a: #f4efe8;
    --photo-b: #b88a6e;
    --photo-c: #7b4a3a;
    --swoosh-dark: #2a2a2a;
    position: absolute; top: 258px; width: 493px; height: 635px;
    background: #fff; overflow: hidden; color: var(--ink);
  }
  .flyer--color { left: 47px; }
  .flyer--grey {
    left: 665px;
    --accent: #7a7a7a;
    --accent-deep: #505050;
    --accent-top: #8c8c8c;
    --photo-a: #f2f2f2;
    --photo-b: #9a9a9a;
    --photo-c: #4e4e4e;
  }
  .flyer__art { position: absolute; inset: 0; width: 493px; height: 635px; }
  .flyer__art .accent-fill { fill: var(--accent); }
  .flyer__art .accent-stroke { stroke: var(--accent); }
  .flyer__art .dark-stroke { stroke: var(--swoosh-dark); }

  .brand {
    position: absolute; left: 25px; top: 33px;
    font-family: "Rubik", sans-serif; font-weight: 800; font-size: 17px;
    letter-spacing: 0.5px; color: var(--ink);
  }
  .headline { position: absolute; left: 24px; top: 128px; font-family: "Anton", sans-serif; line-height: 1; }
  .headline__line { display: block; color: var(--ink); }
  .headline__line--our { font-size: 36px; }
  .headline__line--plans { font-size: 35px; color: var(--accent); margin-top: 3px; }
  .headline__line--based { font-size: 22px; margin-top: 3px; }

  .section-title {
    position: absolute; font-family: "Rubik", sans-serif; font-weight: 700;
    font-size: 10px; color: var(--accent);
  }
  .section-title--mpi { left: 25px; top: 296px; }
  .section-title--also { left: 293px; top: 458px; }

  .intro { position: absolute; left: 25px; top: 321px; width: 206px; font-size: 7.2px; line-height: 9.4px; color: #333; }
  .intro p { text-align: justify; margin-bottom: 5px; }
  .intro p.gap { margin-top: 8px; }

  .benefits {
    position: absolute; left: 287px; top: 212px; width: 187px; height: 225px;
    border-radius: 15px;
    background: linear-gradient(180deg, var(--accent-top) 0%, var(--accent-deep) 100%);
  }
  .benefits__tab {
    position: absolute; left: 278px; top: 231px; height: 18px; padding: 0 10px 0 20px;
    background: #2c2c2c; border-radius: 0 9px 9px 0;
    font-family: "Rubik", sans-serif; font-weight: 500; font-size: 13px; line-height: 18px; color: #fff;
  }
  .benefits__list { position: absolute; left: 300px; top: 266px; width: 160px; list-style: none; }
  .benefits__item {
    position: relative; padding-left: 17px; color: #fff;
    font-family: "Lato", sans-serif; font-weight: 700; font-size: 7px; line-height: 9.4px; margin-bottom: 9px;
  }
  .tick { position: absolute; left: 0; top: 1px; width: 9px; height: 9px; }
  .benefits__item .tick circle, .benefits__item .tick path { stroke: #fff; }

  .specialties { position: absolute; left: 293px; top: 476px; list-style: none; }
  .specialties__item { position: relative; padding-left: 16px; font-size: 8.3px; line-height: 10px; color: #333; margin-bottom: 10px; }
  .specialties__item .tick { top: 1px; }
  .specialties__item .tick circle, .specialties__item .tick path { stroke: var(--accent); }

  .contact { position: absolute; left: 0; top: 0; width: 493px; height: 635px; color: #fff; font-family: "Rubik", sans-serif; }
  .contact__label { position: absolute; left: 25px; top: 568px; font-size: 15px; font-weight: 500; }
  .contact__phone { position: absolute; left: 24px; top: 584px; font-size: 25px; font-weight: 500; letter-spacing: 0.2px; }
  .contact__item { position: absolute; top: 584px; display: flex; align-items: center; gap: 6px; font-size: 6.4px; font-weight: 700; }
  .contact__item--mail { left: 217px; }
  .contact__item--web { left: 366px; }
  .contact__icon { width: 18px; height: 18px; }
  .contact__social { position: absolute; left: 452px; top: 607px; display: flex; gap: 2px; }
  .contact__social span { width: 6px; height: 6px; background: #fff; display: block; }
</style>
</head>
<body>
  <div class="board-half board-half--color"></div>
  <div class="board-half board-half--grey"></div>

  <!-- full colour version -->
  <article class="flyer flyer--color">
    <svg class="flyer__art" viewBox="0 0 493 635" aria-hidden="false">
      <defs>
        <linearGradient id="photoTone1" x1="0" x2="1" y1="0" y2="0">
          <stop offset="0.2" stop-color="var(--photo-a)" stop-opacity="1"/>
          <stop offset="0.55" stop-color="var(--photo-b)"/>
          <stop offset="1" stop-color="var(--photo-c)"/>
        </linearGradient>
        <linearGradient id="footerTone1" x1="0" x2="0" y1="0" y2="1">
          <stop offset="0" stop-color="var(--accent-top)"/>
          <stop offset="1" stop-color="var(--accent-deep)"/>
        </linearGradient>
      </defs>
      <rect x="0" y="0" width="493" height="262" fill="url(#photoTone1)" role="img" aria-label="Photo of a young family sitting on the front steps of their new home"/>
      <path d="M0 0 H270 C210 70 120 103 0 105 Z" fill="#fff"/>
      <path d="M0 104 C120 100 210 70 270 0" fill="none" class="dark-stroke" stroke-width="5"/>
      <path d="M0 109 C125 106 215 72 278 0" fill="none" class="accent-stroke" stroke-width="2"/>
      <path d="M0 240 C150 272 330 262 493 210 V635 H0 Z" fill="#fff"/>
      <path d="M0 236 C150 268 330 258 493 206" fill="none" class="dark-stroke" stroke-width="7"/>
      <path d="M0 251 C150 280 330 270 493 216" fill="none" class="accent-stroke" stroke-width="2"/>
      <path d="M0 560 C80 520 170 552 260 560 C350 568 430 545 493 517 V635 H0 Z" fill="url(#footerTone1)"/>
      <path d="M0 552 C80 512 170 544 260 552 C350 560 430 537 493 509" fill="none" class="dark-stroke" stroke-width="4"/>
    </svg>

    <div class="brand">CORVANT SHIELD</div>

    <h1 class="headline">
      <span class="headline__line headline__line--our">OUR</span>
      <span class="headline__line headline__line--plans">PLANS ARE</span>
      <span class="headline__line headline__line--based">BASED ON YOURS</span>
    </h1>

    <div class="benefits"></div>
    <div class="benefits__tab">Benefits:</div>
    <ul class="benefits__list">
      <li class="benefits__item"><svg class="tick" viewBox="0 0 10 10"><circle cx="5" cy="5" r="4.3" fill="none" stroke-width="0.9"/><path d="M3 5.2 L4.5 6.6 L7.2 3.7" fill="none" stroke-width="0.9"/></svg>Guaranteed approval. Even if you’re in poor health or work in a dangerous profession, there is guaranteed approval with no medical exams or lab tests.</li>
      <li class="benefits__item"><svg class="tick" viewBox="0 0 10 10"><circle cx="5" cy="5" r="4.3" fill="none" stroke-width="0.9"/><path d="M3 5.2 L4.5 6.6 L7.2 3.7" fill="none" stroke-width="0.9"/></svg>No guesswork. The check goes straight to the lender for the exact mortgage balance, so there’ll always be enough and your family won’t have to handle the money.</li>
      <li class="benefits__item"><svg class="tick" viewBox="0 0 10 10"><circle cx="5" cy="5" r="4.3" fill="none" stroke-width="0.9"/><path d="M3 5.2 L4.5 6.6 L7.2 3.7" fill="none" stroke-width="0.9"/></svg>Disability protection. Many MPI policies make mortgage payments (usually for a limited time) if you become disabled or lose your job.</li>
    </ul>

    <h2 class="section-title section-title--mpi">Mortgage Protection Insurance</h2>
    <div class="intro">
      <p>Mortgage Protection Insurance (MPI) is a type of decreasing term life insurance policy designed to pay off your mortgage if you were to pass away — and many policies also cover mortgage payments (usually for a limited period of time) if you become disabled.</p>
      <p>Unforeseen events and a lack of the right kind of insurance can spell trouble quickly. Contact us today, to set up a free assessment time. We will analyze your insurance needs and get you and your family the right coverage quickly at a budget friendly price.</p>
      <p class="gap">We have been helping clients in Northern Idaho/Eastern Washington prepare for the unknown.</p>
      <p class="gap">We have access to the industry’s top insurance carriers so you can get the right coverage, that fits your budget.</p>
      <p>Find out how we can give you the peace of mind of knowing your family will not have a financial burden if something were to happen to you.</p>
    </div>

    <h2 class="section-title section-title--also">We Also Specialize In:</h2>
    <ul class="specialties">
      <li class="specialties__item"><svg class="tick" viewBox="0 0 10 10"><circle cx="5" cy="5" r="4.3" fill="none" stroke-width="0.9"/><path d="M3 5.2 L4.5 6.6 L7.2 3.7" fill="none" stroke-width="0.9"/></svg>Medicare Supplement<br>Insurance (Medigap)</li>
      <li class="specialties__item"><svg class="tick" viewBox="0 0 10 10"><circle cx="5" cy="5" r="4.3" fill="none" stroke-width="0.9"/><path d="M3 5.2 L4.5 6.6 L7.2 3.7" fill="none" stroke-width="0.9"/></svg>Final Expense Insurance</li>
      <li class="specialties__item"><svg class="tick" viewBox="0 0 10 10"><circle cx="5" cy="5" r="4.3" fill="none" stroke-width="0.9"/><path d="M3 5.2 L4.5 6.6 L7.2 3.7" fill="none" stroke-width="0.9"/></svg>Annuities</li>
    </ul>

    <div class="contact">
      <div class="contact__label">Call us now:</div>
      <div class="contact__phone">(208)555.0147</div>
      <div class="contact__item contact__item--mail">
        <svg class="contact__icon" viewBox="0 0 18 18"><circle cx="9" cy="9" r="8" fill="none" stroke="#fff" stroke-width="0.9"/><rect x="5" y="6" width="8" height="6" fill="none" stroke="#fff" stroke-width="0.9"/><path d="M5 6 L9 9.5 L13 6" fill="none" stroke="#fff" stroke-width="0.9"/></svg>
        <span>tkelwer@corvantshield.com</span>
      </div>
      <div class="contact__item contact__item--web">
        <svg class="contact__icon" viewBox="0 0 18 18"><circle cx="9" cy="9" r="8" fill="none" stroke="#fff" stroke-width="0.9"/><circle cx="9" cy="9" r="4.5" fill="none" stroke="#fff" stroke-width="0.8"/><ellipse cx="9" cy="9" rx="2" ry="4.5" fill="none" stroke="#fff" stroke-width="0.8"/><path d="M4.5 9 H13.5" stroke="#fff" stroke-width="0.8"/></svg>
        <span>corvantshield.com</span>
      </div>
      <div class="contact__social"><span></span><span></span></div>
    </div>
  </article>

  <!-- greyscale version -->
  <article class="flyer flyer--grey">
    <svg class="flyer__art" viewBox="0 0 493 635">
      <defs>
        <linearGradient id="photoTone2" x1="0" x2="1" y1="0" y2="0">
          <stop offset="0.2" stop-color="var(--photo-a)"/>
          <stop offset="0.55" stop-color="var(--photo-b)"/>
          <stop offset="1" stop-color="var(--photo-c)"/>
        </linearGradient>
        <linearGradient id="footerTone2" x1="0" x2="0" y1="0" y2="1">
          <stop offset="0" stop-color="var(--accent-top)"/>
          <stop offset="1" stop-color="var(--accent-deep)"/>
        </linearGradient>
      </defs>
      <rect x="0" y="0" width="493" height="262" fill="url(#photoTone2)" role="img" aria-label="Greyscale photo of a young family sitting on the front steps of their new home"/>
      <path d="M0 0 H270 C210 70 120 103 0 105 Z" fill="#fff"/>
      <path d="M0 104 C120 100 210 70 270 0" fill="none" class="dark-stroke" stroke-width="5"/>
      <path d="M0 109 C125 106 215 72 278 0" fill="none" class="accent-stroke" stroke-width="2"/>
      <path d="M0 240 C150 272 330 262 493 210 V635 H0 Z" fill="#fff"/>
      <path d="M0 236 C150 268 330 258 493 206" fill="none" class="dark-stroke" stroke-width="7"/>
      <path d="M0 251 C150 280 330 270 493 216" fill="none" class="accent-stroke" stroke-width="2"/>
      <path d="M0 560 C80 520 170 552 260 560 C350 568 430 545 493 517 V635 H0 Z" fill="url(#footerTone2)"/>
      <path d="M0 552 C80 512 170 544 260 552 C350 560 430 537 493 509" fill="none" class="dark-stroke" stroke-width="4"/>
    </svg>

    <div class="brand">CORVANT SHIELD</div>

    <h1 class="headline">
      <span class="headline__line headline__line--our">OUR</span>
      <span class="headline__line headline__line--plans">PLANS ARE</span>
      <span class="headline__line headline__line--based">BASED ON YOURS</span>
    </h1>

    <div class="benefits"></div>
    <div class="benefits__tab">Benefits:</div>
    <ul class="benefits__list">
      <li class="benefits__item"><svg class="tick" viewBox="0 0 10 10"><circle cx="5" cy="5" r="4.3" fill="none" stroke-width="0.9"/><path d="M3 5.2 L4.5 6.6 L7.2 3.7" fill="none" stroke-width="0.9"/></svg>Guaranteed approval. Even if you’re in poor health or work in a dangerous profession, there is guaranteed approval with no medical exams or lab tests.</li>
      <li class="benefits__item"><svg class="tick" viewBox="0 0 10 10"><circle cx="5" cy="5" r="4.3" fill="none" stroke-width="0.9"/><path d="M3 5.2 L4.5 6.6 L7.2 3.7" fill="none" stroke-width="0.9"/></svg>No guesswork. The check goes straight to the lender for the exact mortgage balance, so there’ll always be enough and your family won’t have to handle the money.</li>
      <li class="benefits__item"><svg class="tick" viewBox="0 0 10 10"><circle cx="5" cy="5" r="4.3" fill="none" stroke-width="0.9"/><path d="M3 5.2 L4.5 6.6 L7.2 3.7" fill="none" stroke-width="0.9"/></svg>Disability protection. Many MPI policies make mortgage payments (usually for a limited time) if you become disabled or lose your job.</li>
    </ul>

    <h2 class="section-title section-title--mpi">Mortgage Protection Insurance</h2>
    <div class="intro">
      <p>Mortgage Protection Insurance (MPI) is a type of decreasing term life insurance policy designed to pay off your mortgage if you were to pass away — and many policies also cover mortgage payments (usually for a limited period of time) if you become disabled.</p>
      <p>Unforeseen events and a lack of the right kind of insurance can spell trouble quickly. Contact us today, to set up a free assessment time. We will analyze your insurance needs and get you and your family the right coverage quickly at a budget friendly price.</p>
      <p class="gap">We have been helping clients in Northern Idaho/Eastern Washington prepare for the unknown.</p>
      <p class="gap">We have access to the industry’s top insurance carriers so you can get the right coverage, that fits your budget.</p>
      <p>Find out how we can give you the peace of mind of knowing your family will not have a financial burden if something were to happen to you.</p>
    </div>

    <h2 class="section-title section-title--also">We Also Specialize In:</h2>
    <ul class="specialties">
      <li class="specialties__item"><svg class="tick" viewBox="0 0 10 10"><circle cx="5" cy="5" r="4.3" fill="none" stroke-width="0.9"/><path d="M3 5.2 L4.5 6.6 L7.2 3.7" fill="none" stroke-width="0.9"/></svg>Medicare Supplement<br>Insurance (Medigap)</li>
      <li class="specialties__item"><svg class="tick" viewBox="0 0 10 10"><circle cx="5" cy="5" r="4.3" fill="none" stroke-width="0.9"/><path d="M3 5.2 L4.5 6.6 L7.2 3.7" fill="none" stroke-width="0.9"/></svg>Final Expense Insurance</li>
      <li class="specialties__item"><svg class="tick" viewBox="0 0 10 10"><circle cx="5" cy="5" r="4.3" fill="none" stroke-width="0.9"/><path d="M3 5.2 L4.5 6.6 L7.2 3.7" fill="none" stroke-width="0.9"/></svg>Annuities</li>
    </ul>

    <div class="contact">
      <div class="contact__label">Call us now:</div>
      <div class="contact__phone">(208)555.0147</div>
      <div class="contact__item contact__item--mail">
        <svg class="contact__icon" viewBox="0 0 18 18"><circle cx="9" cy="9" r="8" fill="none" stroke="#fff" stroke-width="0.9"/><rect x="5" y="6" width="8" height="6" fill="none" stroke="#fff" stroke-width="0.9"/><path d="M5 6 L9 9.5 L13 6" fill="none" stroke="#fff" stroke-width="0.9"/></svg>
        <span>tkelwer@corvantshield.com</span>
      </div>
      <div class="contact__item contact__item--web">
        <svg class="contact__icon" viewBox="0 0 18 18"><circle cx="9" cy="9" r="8" fill="none" stroke="#fff" stroke-width="0.9"/><circle cx="9" cy="9" r="4.5" fill="none" stroke="#fff" stroke-width="0.8"/><ellipse cx="9" cy="9" rx="2" ry="4.5" fill="none" stroke="#fff" stroke-width="0.8"/><path d="M4.5 9 H13.5" stroke="#fff" stroke-width="0.8"/></svg>
        <span>corvantshield.com</span>
      </div>
      <div class="contact__social"><span></span><span></span></div>
    </div>
  </article>
</body>
</html>
```